Business card design needed to incorporate existing logo

We need a business card for a new modern Accounting & Business Solutions company call TelmaNord Partners.com.au servicing all of Australia.
My tagline is Steady Ledger Answers... that deliver.

We specialise in Cloud Accounting and this is our primary focus. We also provide tax representation, debt recovery, computer, tablet and smart phone sales.

I would like a design that uses my corporate, trustworthy colours of blue/white, black/grey however am open to suggestion. I have attached my logo to go on the card somewhere,of which you will see the colour scheme.

I am after a card that STANDS OUT, somewhere between it not being too busy and not being a baron waste of space.

A 'cloud' incorporated in the design may work well, up to your artistic judgement. I know what I like when I see it; it is harder to put into words!

Excited to see your ideas!
I have added my logo predominately (blue/white) and for additional opportunity have added my reverse logo (darker one). I have used the blue/white on my website and letterhead. I will be using both on my vehicle signage.

Target Market(s)

Tradesmen and small-medium businesses of all descriptions Australia-wide

Industry/Entity Type

Debt

Contact Information for Business Card

Doug Hallett
Principal (optional)
TelmaNord Partners.com.au
Steady Ledger Answers... that deliver

P: 1800 493 518
M: 0412 658 071 (optional)
W: www.telmanordpartners.com.au
E: admin@telmanordpartners.com.au

Logo Text

Steady Ledger Answers... that deliver!

Logo styles of interest
Wordmark Logo
Requirements
Must have
• Must look professional and of high quality not cheap.

My logo and my tagline 'Steady Ledger Answers... that deliver'.

I have my colourscheme in mind as per my attached logo, however am open to suggestion. I want to see what you can create that I would not have thought of.

Modern, innovative.
Something I won't look at and think, 'I could have done that myself'.

Must be able to be printed on Prinvo 300gm premium cards and the artwork provided to me.
Nice to have
• Title of Principal is optional depending on space and judement call of look/fee.
M: (mobile) number is also optional as above.

Somthing cloud related given the Cloud Accounting aspect may be relevant. I leave it to your artistic design and judgement.
Should not have
• Must not look cheap.

```html
<!DOCTYPE html>
<html lang="en">
<head>
<meta charset="utf-8">
<title>TelmaNord Partners – Business Card</title>
<link rel="stylesheet" href="https://fonts.googleapis.com/css2?family=Raleway:wght@300&family=Montserrat:wght@500;700&display=swap">
<style>
  :root {
    --backdrop: #1b1d22;
    --navy: #16235a;
    --navy-deep: #0f1a47;
    --brand-blue: #2a86c8;
    --sky: #5fb2e6;
    --ink: #1a1a1a;
    --grey: #4a4f57;
    --white: #ffffff;
  }
  * { margin: 0; padding: 0; box-sizing: border-box; }
  html, body {
    width: 1200px; height: 675px; overflow: hidden;
    background: var(--backdrop);
  }
  .stage {
    width: 1200px; height: 675px;
    display: flex; align-items: center; justify-content: center; gap: 60px;
  }
  .card {
    position: relative;
    width: 520px; height: 318px;
    border-radius: 4px;
    overflow: hidden;
    box-shadow: 0 10px 30px rgba(0,0,0,.45);
  }

  /* Front */
  .card--front { background: var(--white); }
  .brand-graphic {
    position: absolute; left: 0; top: 0;
    width: 215px; height: 100%;
    background: linear-gradient(160deg, #7d8fc0 0%, var(--brand-blue) 55%, #1e6fb0 100%);
    opacity: .9;
  }
  .wordmark {
    font-family: "Raleway", sans-serif;
    font-weight: 300;
    color: var(--brand-blue);
    line-height: 1.05;
  }
  .card--front .wordmark {
    position: absolute; left: 262px; top: 40px;
    font-size: 25px; letter-spacing: 2px;
  }
  .wordmark .sub { display: block; font-size: 13px; letter-spacing: 4px; margin-top: 4px; }
  .contact {
    position: absolute; left: 262px; top: 150px;
    font-family: "Montserrat", sans-serif;
  }
  .contact__name { font-weight: 700; font-size: 15px; color: var(--brand-blue); }
  .contact__role { font-weight: 500; font-size: 13px; color: var(--ink); margin-bottom: 8px; }
  .contact__line {
    display: flex; align-items: center; gap: 7px;
    font-size: 10.5px; font-weight: 500; color: var(--grey); line-height: 1.55;
  }
  .contact__line svg { width: 10px; height: 10px; fill: var(--navy); flex: none; }
  .website {
    position: absolute; left: 238px; bottom: 26px;
    font-family: "Montserrat", sans-serif; font-weight: 500; font-size: 11.5px;
    color: var(--ink);
  }
  .website .domain { color: var(--brand-blue); }

  /* Back */
  .card--back {
    background: radial-gradient(circle at 50% 45%, #1f2f72 0%, var(--navy) 55%, var(--navy-deep) 100%);
    display: flex; align-items: center; justify-content: center;
  }
  .card--back .wordmark { color: var(--sky); font-size: 38px; letter-spacing: 3px; text-align: center; }
  .card--back .wordmark .sub { font-size: 17px; letter-spacing: 6px; margin-top: 6px; }
</style>
</head>
<body>
<main class="stage">
  <section class="card card--front">
    <div class="brand-graphic" role="img" aria-label="Large brand graphic in blue tones"></div>
    <div class="wordmark">TelmaNord<span class="sub">PARTNERS.COM.AU</span></div>
    <div class="contact">
      <p class="contact__name">Doug Hallett</p>
      <p class="contact__role">Principal</p>
      <p class="contact__line">
        <svg viewBox="0 0 10 10" aria-hidden="true"><rect x="2" y="0" width="6" height="10" rx="1.2"/></svg>
        1800 493 518
      </p>
      <p class="contact__line">
        <svg viewBox="0 0 10 10" aria-hidden="true"><path d="M1 3c0-1 1-2 4-2s4 1 4 2v1H7V3H3v1H1zM2 5h6l1 4H1z"/></svg>
        0412 658 071
      </p>
      <p class="contact__line">
        <svg viewBox="0 0 10 10" aria-hidden="true"><path d="M0 2h10v6H0zM0 2l5 3.5L10 2" stroke="#fff" stroke-width=".8"/></svg>
        admin@telmanordpartners.com.au
      </p>
    </div>
    <p class="website">www.<span class="domain">telmanordpartners</span>.com.au</p>
  </section>

  <section class="card card--back">
    <div class="wordmark">TelmaNord<span class="sub">PARTNERS.COM.AU</span></div>
  </section>
</main>
</body>
</html>
```